Business Card Design Project

We are not a new company, but renamed to "Vantorin Kitchens" last year. We specialize in modern high-end cabinetry imports. We would like to communicate a sense of quality and cutting edge technology. Ideally the design would incorporate our logo colors, silver, red and preferably a black, matte background. Though we are open to suggestions.
Logo is attached.
Edit: I have attached rough drafts of the previous cards, this way you will have all necessary content that needs to go on the cards.
Updates
Project Deadline Extended
Reason: We have received a lot of great designs, but due to the sheer number we couldn't respond to all. We will extend the deadline for another 7 days to finalize and provide feedback to designers.
Thank you for your hard work!
Industry/Entity Type
Business
Look and feel
Each slider illustrates characteristics of the customer's brand and the style your logo design should communicate.

```html
<!DOCTYPE html>
<html lang="en">
<head>
<meta charset="utf-8">
<title>Vantorin Kitchens – Business Card</title>
<link href="https://fonts.googleapis.com/css2?family=Michroma&family=Arimo:wght@400;700&display=swap" rel="stylesheet">
<style>
  :root{
    --page:#e9e9ee;
    --black:#121212;
    --black-soft:#3a3a3a;
    --silver:#a9a9ad;
    --silver-light:#d4d4d8;
    --grey-band:#8e8e92;
    --red:#e41e26;
    --white:#ffffff;
  }
  *{box-sizing:border-box;margin:0;padding:0}
  html,body{width:1200px;height:987px;overflow:hidden;background:var(--page)}
  body{font-family:"Arimo",Arial,sans-serif}
  .card{
    position:absolute;left:250px;width:700px;height:400px;border-radius:22px;overflow:hidden;
    background:radial-gradient(ellipse at 40% 45%,var(--black-soft) 0%,var(--black) 70%);
    box-shadow:0 12px 30px rgba(0,0,0,.18);
  }
  .card--front{top:50px}
  .card--back{top:520px}
  .card__curves{position:absolute;inset:0}
  .wordmark{
    position:absolute;font-family:"Michroma",Arial,sans-serif;color:var(--silver-light);
    letter-spacing:1px;white-space:nowrap;display:flex;align-items:center;gap:10px;
  }
  .wordmark__square{width:24px;height:24px;background:var(--silver)}
  .card--front .wordmark{left:36px;top:168px;font-size:20px}
  .card--back .wordmark{left:50%;top:50%;transform:translate(-50%,-50%);font-size:36px;gap:14px;letter-spacing:2px}
  .card--back .wordmark__square{width:40px;height:40px}
  .contact{position:absolute;left:36px;top:250px;list-style:none;color:var(--white);font-size:16px;line-height:27px}
  .contact li{display:flex;align-items:center;gap:10px}
  .contact svg{width:14px;height:14px;fill:var(--red)}
  .divider{position:absolute;left:320px;top:268px;width:1px;height:92px;background:var(--silver)}
  .address{position:absolute;left:338px;top:290px;color:var(--white);font-size:17px;line-height:28px;font-style:normal}
  .person{position:absolute;right:24px;top:150px;text-align:right;color:var(--white)}
  .person__name{font-size:20px;font-weight:700;letter-spacing:.3px}
  .person__role{font-size:16px;font-weight:700;margin-top:3px}
</style>
</head>
<body>
  <section class="card card--front">
    <svg class="card__curves" viewBox="0 0 700 400" aria-hidden="true">
      <path d="M0,28 C420,30 540,180 560,400 H700 V0 H0 Z" fill="var(--grey-band)"/>
      <path d="M0,28 C420,30 540,180 560,400" fill="none" stroke="var(--red)" stroke-width="10"/>
      <path d="M0,42 C400,44 520,190 540,400" fill="none" stroke="var(--black)" stroke-width="3"/>
    </svg>
    <div class="wordmark"><span class="wordmark__square"></span>VANTORIN KITCHENS</div>
    <ul class="contact">
      <li><svg viewBox="0 0 16 16"><path d="M3 1h3l1 4-2 1c1 2 3 4 5 5l1-2 4 1v3c0 1-1 2-2 2C7 15 1 9 1 3c0-1 1-2 2-2z"/></svg>780.555.0142</li>
      <li><svg viewBox="0 0 16 16"><path d="M2 5h12v8H2zM5 2h6v3H5z"/></svg>780.555.0187</li>
      <li><svg viewBox="0 0 16 16"><path d="M4 1h8v14H4zM6 3v8h4V3z"/></svg>780.555.0263</li>
      <li><svg viewBox="0 0 16 16"><path d="M1 3h14v10H1zM2 4l6 5 6-5z"/></svg>marcus@vantorinkitchens.ca</li>
    </ul>
    <div class="divider"></div>
    <address class="address">5120 - 87 Ave.<br>Calgary, AB T2K 4R8</address>
    <div class="person">
      <div class="person__name">MARCUS DELLER</div>
      <div class="person__role">Director</div>
    </div>
  </section>
  <section class="card card--back">
    <div class="wordmark"><span class="wordmark__square"></span>VANTORIN KITCHENS</div>
  </section>
</body>
</html>
```